Corven Hale Interiors Web Site

We are looking at web site for our start-up company which is located in Abu Dhabi United Arab Emirates. Our main business activity is Interior fit out for high medium to high end projects in residential, corporate and hospitality.
In terms of look and feel the web site should be vibrant yet professional reflecting the artistic/construction nature of our business and built along or allows the following aspects:
- Number of Pages: 8-10 main pages (Including 10 Sub Pages)
- A custom responsive web design compatible with all browsers
- Dynamic (admin panel). CMS
- Anti Spam Online Forms
- Photo & Video Gallery
- Mobile Ready (Iphone,Android)]
- Social Media Integration
- Google Map
- Banner Artworks

```html
<!DOCTYPE html>
<html lang="en">
<head>
<meta charset="utf-8">
<title>Corven Hale Interiors</title>
<link href="https://fonts.googleapis.com/css2?family=Cabin:wght@400;600;700&display=swap" rel="stylesheet">
<style>
:root{
  --panel:#4e6373;
  --panel-dark:#3c4d5a;
  --logo-bg:#d8d8d6;
  --ink:#3a3f44;
  --white:#ffffff;
  --nav-active:#8ec3e0;
  --footer:#121212;
  --footer-line:#3a3a3a;
  --footer-text:#8c8c8c;
}
*{margin:0;padding:0;box-sizing:border-box}
html,body{width:729px;height:1200px;overflow:hidden}
body{position:relative;font-family:"Cabin",sans-serif;color:var(--white);background:var(--footer)}
.backdrop{position:absolute;left:0;top:0;width:729px;height:1066px;
  background:linear-gradient(180deg,#e9e5de 0%,#c9a26a 18%,#b27c3c 45%,#8f5d2a 65%,#d8c8b0 80%,#6b4a2a 100%)}
.logo{position:absolute;left:110px;top:0;width:141px;height:122px;background:var(--logo-bg);
  display:flex;flex-direction:column;align-items:center;justify-content:center;color:var(--ink);font-weight:600}
.logo-mark{width:24px;height:24px;background:var(--panel);margin-bottom:10px}
.logo-name{font-size:18px;line-height:1}
.logo-sub{font-size:9px;letter-spacing:4px;margin-top:6px}
.nav{position:absolute;top:59px;left:0;font-size:8px;font-weight:600;text-transform:uppercase}
.nav a{position:absolute;color:var(--white);text-decoration:none;white-space:nowrap}
.nav a.active{color:var(--nav-active)}
.nav a.active::before{content:"";position:absolute;left:-3px;right:-3px;top:-10px;height:2px;background:var(--nav-active)}
.hero{position:absolute;left:110px;top:135px;width:510px;height:285px;
  background:linear-gradient(180deg,#ececea 0%,#dcdcd8 55%,#b9b4ac 75%,#cfcac2 100%)}
.hero-arrow{position:absolute;top:127px;width:31px;height:31px;background:rgba(40,40,40,.75)}
.hero-arrow.prev{left:0}.hero-arrow.next{right:0}
.hero-caption{position:absolute;left:0;bottom:0;width:245px;height:56px;background:var(--panel);
  font-size:14px;font-weight:700;padding:22px 0 0 20px;text-transform:uppercase}
.card{position:absolute;top:446px;width:163px;height:252px;background:var(--panel)}
.card h2{height:42px;font-size:12px;font-weight:700;text-transform:uppercase;padding:15px 0 0 14px}
.card-photo{height:106px}
.card p{font-size:8px;line-height:12.5px;padding:12px 12px 0 12px}
.card .btn{position:absolute;left:14px;top:218px;height:22px;padding:0 6px;background:var(--panel-dark);
  font-size:8px;line-height:22px}
.testimonial{position:absolute;left:110px;top:727px;width:510px;height:103px;background:var(--panel)}
.avatar{position:absolute;left:20px;top:20px;width:64px;height:64px;border-radius:50%;background:linear-gradient(180deg,#f1f1f1,#c9c9c9)}
.quote{position:absolute;left:99px;top:22px;width:395px;font-size:8px;line-height:12.5px}
.author{position:absolute;left:99px;top:75px;font-size:8.5px}
.dots{position:absolute;left:239px;top:82px;display:flex;gap:7px}
.dots span{width:5px;height:5px;border-radius:50%;background:#8796a1}
.dots span.on{background:var(--white)}
.gallery-title{position:absolute;left:110px;top:862px;font-size:11.5px;text-transform:uppercase}
.view-more{position:absolute;right:110px;top:867px;font-size:6px;text-transform:uppercase}
.tile{position:absolute;width:127px;height:73px}
.tile.text{background:var(--panel);padding:11px 8px 0}
.tile h3{font-size:8px;font-weight:400;text-transform:uppercase;margin-bottom:6px}
.tile p{font-size:6px;line-height:9px}
.play{position:absolute;left:54px;top:27px}
.footer{position:absolute;left:0;top:1066px;width:729px;height:134px;background:var(--footer)}
.social{position:absolute;left:268px;top:40px}
.copyright{position:absolute;left:0;width:729px;top:101px;text-align:center;font-size:8px;color:var(--footer-text)}
</style>
</head>
<body>
<div class="backdrop" role="img" aria-label="Warm wood-panelled bedroom interior with lamps and bed"></div>

<div class="logo">
  <div class="logo-mark"></div>
  <div class="logo-name">Corven Hale</div>
  <div class="logo-sub">Interiors</div>
</div>

<nav class="nav">
  <a class="active" style="left:342px">Home</a>
  <a style="left:398px">Projects</a>
  <a style="left:465px">News</a>
  <a style="left:520px">Gallery</a>
  <a style="left:585px">Contact</a>
</nav>

<section class="hero">
  <div role="img" aria-label="Modern living room with white sofa, wooden coffee table and lamps" style="position:absolute;inset:0"></div>
  <div class="hero-arrow prev"><svg width="31" height="31"><polyline points="18,10 12,15.5 18,21" fill="none" stroke="#fff" stroke-width="1.5"/></svg></div>
  <div class="hero-arrow next"><svg width="31" height="31"><polyline points="13,10 19,15.5 13,21" fill="none" stroke="#fff" stroke-width="1.5"/></svg></div>
  <div class="hero-caption">Modern Living Room Design</div>
</section>

<article class="card" style="left:110px">
  <h2>Our Company</h2>
  <div class="card-photo" role="img" aria-label="Living room with brown armchairs and television unit" style="background:linear-gradient(180deg,#e8e2d8,#a4684a 70%,#7a4a30)"></div>
  <p>Lorem ipsum dolor sit amet, consecte-tur adipisicing elit, sed do eiusmod tempor incididunt ut labore et dolore magna aliqua.</p>
  <span class="btn">Read More</span>
</article>
<article class="card" style="left:283px">
  <h2>Latest Technologies</h2>
  <div class="card-photo" role="img" aria-label="Fireplace wall with bookshelves and two yellow armchairs" style="background:linear-gradient(180deg,#efe6da,#e8b84a 65%,#f0a020)"></div>
  <p>Lorem ipsum dolor sit amet, consecte-tur adipisicing elit, sed do eiusmod tempor incididunt ut labore et dolore magna aliqua.</p>
  <span class="btn">Read More</span>
</article>
<article class="card" style="left:456px">
  <h2>Design Tips</h2>
  <div class="card-photo" role="img" aria-label="Bright lounge with white sofa, plant and fireplace" style="background:linear-gradient(180deg,#e6e2d6,#b9a878 60%,#eae6de)"></div>
  <p>Lorem ipsum dolor sit amet, consecte-tur adipisicing elit, sed do eiusmod tempor incididunt ut labore et dolore magna aliqua.</p>
  <span class="btn">Read More</span>
</article>

<section class="testimonial">
  <div class="avatar" role="img" aria-label="Portrait of client"></div>
  <p class="quote">Lorem ipsum dolor sit amet, consectetur adipisicing elit, sed do eiusmod tempor incididunt ut labore et dolore magna aliqua. Ut enim ad minim veniam, quis nostrud exercitation ullamco laboris nisi ut aliquip ex ea commodo consequat.</p>
  <div class="author">John Smith</div>
  <div class="dots"><span class="on"></span><span></span><span></span></div>
</section>

<h2 class="gallery-title">Our Photo &amp; Video Gallery</h2>
<span class="view-more">View More</span>

<div class="tile" style="left:110px;top:894px;background:linear-gradient(135deg,#8a5a32,#e2d2b8)" role="img" aria-label="Wooden bathroom with glass shower"></div>
<div class="tile text" style="left:236px;top:894px"><h3>The Standard Lorem</h3><p>Lorem ipsum dolor sit amet, consecte-tur adipiscing elit, sed do eiusmod</p></div>
<div class="tile" style="left:364px;top:894px;background:linear-gradient(180deg,#3f6f95,#8fb0c8 60%,#c8d2da)" role="img" aria-label="Blue striped bathroom, video">
  <svg class="play" width="19" height="19"><circle cx="9.5" cy="9.5" r="8.5" fill="none" stroke="#fff" stroke-width="1.2"/><polyline points="8,5.5 12,9.5 8,13.5" fill="none" stroke="#fff" stroke-width="1.2"/></svg></div>
<div class="tile text" style="left:491px;top:894px;width:128px"><h3>The Standard Lorem</h3><p>Lorem ipsum dolor sit amet, consecte-tur adipiscing elit, sed do eiusmod</p></div>

<div class="tile text" style="left:110px;top:967px"><h3>The Standard Lorem</h3><p>Lorem ipsum dolor sit amet, consecte-tur adipiscing elit, sed do eiusmod</p></div>
<div class="tile" style="left:236px;top:967px;width:128px;background:linear-gradient(180deg,#d8d8d2,#8a4a28 65%,#c9c4bc)" role="img" aria-label="Kitchen with wooden island counter"></div>
<div class="tile text" style="left:364px;top:967px"><h3>The Standard Lorem</h3><p>Lorem ipsum dolor sit amet, consecte-tur adipiscing elit, sed do eiusmod</p></div>
<div class="tile" style="left:491px;top:967px;width:128px;background:linear-gradient(180deg,#3a2a22,#6a5448 50%,#d8d4d0)" role="img" aria-label="Dark bedroom with white bed, video">
  <svg class="play" width="19" height="19"><circle cx="9.5" cy="9.5" r="8.5" fill="none" stroke="#fff" stroke-width="1.2"/><polyline points="8,5.5 12,9.5 8,13.5" fill="none" stroke="#fff" stroke-width="1.2"/></svg></div>

<footer class="footer">
  <svg class="social" width="194" height="34" aria-label="Social links">
    <g fill="none" stroke="var(--footer-line)" stroke-width="1">
      <circle cx="16.5" cy="17" r="16"/><circle cx="56.5" cy="17" r="16"/><circle cx="96.5" cy="17" r="16"/><circle cx="137.5" cy="17" r="16"/><circle cx="177.5" cy="17" r="16"/>
    </g>
    <g fill="none" stroke="#777" stroke-width="1"><rect x="91.5" y="13" width="10" height="8"/><polyline points="91.5,13 96.5,17.5 101.5,13"/></g>
  </svg>
  <p class="copyright">© Copyright 2014 - CorvenHale</p>
</footer>
</body>
</html>
```